Handmade candle business in melbourne requiring assistance with designing classy labels

My business name is Wick and Willow.
I specialise in making handmade candles, i'm based in Melbourne.
My moto is "Delicately hand poured and infused by me...for you"
wickwillow@lanterbox.com
0427 816 093

I need some assistance with designing my labels for my glass candles
I really like earthy colours and nothing too bright, but I want it to look classy and elegant and something that stands out from other homemade candle businesses.
I have attached a sample of a design that appeals to me but open to suggestions.

```html
<!DOCTYPE html>
<html lang="en">
<head>
<meta charset="utf-8">
<title>Wick and Willow – Candle Label</title>
<link rel="stylesheet" href="https://fonts.googleapis.com/css2?family=Pinyon+Script&family=Arimo:wght@700&family=Open+Sans:wght@700&family=Tinos&display=swap">
<style>
  :root {
    --page: #ffffff;
    --ink: #0d0b0a;
    --ring-edge: #a97e5c;
    --ring-mid: #e2cba9;
    --field-edge: #c3a07e;
    --field-mid: #e4cfae;
    --line-warm: #b86a14;
    --line-deep: #5a2408;
    --line-plum: #3d2638;
    --line-gold: #c2901e;
  }
  html, body {
    margin: 0;
    padding: 0;
    width: 1200px;
    height: 1199px;
    overflow: hidden;
    background: var(--page);
  }
  .label {
    display: block;
    width: 1200px;
    height: 1199px;
  }
  .motto-script {
    font-family: "Pinyon Script", cursive;
    fill: var(--ink);
  }
  .brand-name {
    font-family: "Arimo", sans-serif;
    font-weight: 700;
    fill: var(--ink);
  }
  .brand-domain {
    font-family: "Tinos", serif;
    fill: var(--ink);
    letter-spacing: 3px;
  }
  .phone {
    font-family: "Open Sans", sans-serif;
    font-weight: 700;
    fill: var(--ink);
  }
</style>
</head>
<body>
<svg class="label" viewBox="0 0 988 987" xmlns="http://www.w3.org/2000/svg" aria-label="Wick and Willow candle label">
  <defs>
    <linearGradient id="ringTone" x1="0" y1="0" x2="1" y2="0">
      <stop offset="0" stop-color="var(--ring-edge)"/>
      <stop offset="0.5" stop-color="var(--ring-mid)"/>
      <stop offset="1" stop-color="var(--ring-edge)"/>
    </linearGradient>
    <linearGradient id="fieldTone" x1="0" y1="0" x2="1" y2="0">
      <stop offset="0" stop-color="var(--field-edge)"/>
      <stop offset="0.45" stop-color="var(--field-mid)"/>
      <stop offset="0.7" stop-color="var(--field-mid)"/>
      <stop offset="1" stop-color="var(--field-edge)"/>
    </linearGradient>
    <linearGradient id="innerLine" x1="0" y1="0" x2="1" y2="0.3">
      <stop offset="0" stop-color="var(--line-deep)"/>
      <stop offset="0.45" stop-color="var(--line-warm)"/>
      <stop offset="0.8" stop-color="var(--line-plum)"/>
      <stop offset="1" stop-color="var(--line-gold)"/>
    </linearGradient>
  </defs>

  <g class="seal">
    <circle class="seal-ring" cx="494" cy="494" r="492" fill="url(#ringTone)"/>
    <circle class="seal-gap" cx="494" cy="494" r="466" fill="none" stroke="#ffffff" stroke-width="3"/>
    <circle class="seal-field" cx="494" cy="494" r="462" fill="url(#fieldTone)"/>
    <circle class="seal-line" cx="494" cy="494" r="446" fill="none" stroke="url(#innerLine)" stroke-width="4"/>
  </g>

  <g class="motto">
    <text class="motto-script" x="482" y="318" font-size="150" text-anchor="middle" textLength="560" lengthAdjust="spacingAndGlyphs">Delicately</text>
    <text class="motto-script" x="490" y="430" font-size="82" text-anchor="middle" textLength="760" lengthAdjust="spacingAndGlyphs">hand poured and infused</text>
    <text class="motto-script" x="486" y="522" font-size="82" text-anchor="middle" textLength="550" lengthAdjust="spacingAndGlyphs">by me...for you</text>
  </g>

  <g class="contact">
    <text class="brand-name" x="478" y="684" font-size="98" text-anchor="middle" textLength="490" lengthAdjust="spacingAndGlyphs">wickwillow</text>
    <text class="brand-domain" x="270" y="713" font-size="26" textLength="275" lengthAdjust="spacingAndGlyphs">@LANTERBOX.COM</text>
    <text class="phone" x="492" y="802" font-size="54" text-anchor="middle" textLength="356" lengthAdjust="spacingAndGlyphs">0427 816 093</text>
  </g>
</svg>
</body>
</html>
```